Business card for my new company (Accounting firm)

I need a business card for my new business Brightwell Advisory and Ledger SA. Our services are accounting, tax, audit and financial management. Our customers are small companies, start-ups and new companies. The final design has to show financial security, trust and growth. Please find our logo attached to the business card. Text for the business card: Brightwell Advisory and Ledger SA Tomas Varenholt Director and Founder Certified Accountant Tel. 022 418 57 34 tv@clairevalconseil.ch www.clairevalconseil.ch Rue des Vergières 27 1201 Geneva
Target Market(s)
Our customers are small companies, start-ups and new companies.
Industry/Entity Type
Finance And Accounting
Contact Information for Business Card
Claireval Conseil et Comptes SA
Tomas Varenholt
Directeur et Fondateur
Expert-comptable diplômé
Tél. 022 418 57 34
tv@clairevalconseil.ch
www.clairevalconseil.ch
Rue des Vergières 27
1201 Genève

```html
<!DOCTYPE html>
<html lang="en">
<head>
<meta charset="utf-8">
<title>Claireval Conseil et Comptes SA – Business Card</title>
<link rel="stylesheet" href="https://fonts.googleapis.com/css2?family=Lato:wght@400;700&family=Montserrat:wght@500&display=swap">
<style>
  :root {
    --backdrop: #c4c4c4;
    --band-light: #2eb1e2;
    --band-dark: #1f89c9;
    --accent-blue: #27a5dd;
    --icon-blue: #2a8fcf;
    --ink: #3f3f3f;
    --paper: #ffffff;
    --slate: #3d3d3f;
  }
  * { box-sizing: border-box; margin: 0; padding: 0; }
  html, body {
    width: 1200px; height: 802px; overflow: hidden;
    background: var(--backdrop);
  }
  .canvas { position: relative; width: 1200px; height: 802px; }
  .card {
    position: absolute; top: 274px;
    width: 443px; height: 265px;
    box-shadow: 0 3px 6px rgba(0,0,0,.25);
  }
  .card--front { left: 136px; background: var(--paper); }
  .card--back  { left: 624px; background: var(--slate); }

  .brand-band {
    position: absolute; left: 0; top: 0; width: 100%; height: 75px;
    background: linear-gradient(90deg, var(--band-light) 0%, var(--band-light) 60%, var(--band-dark) 78%, var(--band-dark) 100%);
  }
  .brand-name {
    font-family: "Montserrat", sans-serif; font-weight: 500;
    color: #fff; text-transform: uppercase;
    font-size: 15px; letter-spacing: 2px; line-height: 1.35;
  }
  .brand-band .brand-name { position: absolute; left: 32px; top: 18px; width: 220px; }

  .holder { position: absolute; left: 27px; top: 135px; font-family: "Lato", sans-serif; }
  .holder__name { color: var(--accent-blue); font-weight: 700; font-size: 15px; text-transform: uppercase; line-height: 18px; }
  .holder__role { color: var(--ink); font-size: 13px; line-height: 15px; }

  .contact { position: absolute; left: 27px; top: 190px; font-family: "Lato", sans-serif; list-style: none; }
  .contact li { display: flex; align-items: center; gap: 4px; color: var(--ink); font-size: 13px; line-height: 16px; }
  .contact svg { width: 11px; height: 11px; fill: var(--icon-blue); flex: none; }

  .address {
    position: absolute; right: 26px; top: 206px; text-align: right;
    font-family: "Lato", sans-serif; font-style: normal; color: var(--ink); font-size: 13px; line-height: 16px;
  }

  .card--back .brand-name {
    position: absolute; left: 0; right: 0; top: 112px;
    text-align: center; font-size: 17px; letter-spacing: 2.5px;
  }
</style>
</head>
<body>
<main class="canvas">
  <section class="card card--front" aria-label="Card front">
    <header class="brand-band">
      <p class="brand-name">Claireval Conseil et Comptes</p>
    </header>
    <div class="holder">
      <p class="holder__name">SA Tomas Varenholt</p>
      <p class="holder__role">Director and Founder</p>
      <p class="holder__role">Certified Accountant</p>
    </div>
    <ul class="contact">
      <li><svg viewBox="0 0 12 12" aria-hidden="true"><path d="M1 4c0-2 2-3 5-3s5 1 5 3l-2 1-1-1.5H4L3 5zM3 6h6l1 5H2z"/></svg>022 418 57 34</li>
      <li><svg viewBox="0 0 12 12" aria-hidden="true"><path d="M1 2.5h10v7H1zM1.6 3l4.4 3.4L10.4 3v1L6 7.4 1.6 4z" fill-rule="evenodd"/></svg>tv@clairevalconseil.ch</li>
      <li><svg viewBox="0 0 12 12" aria-hidden="true"><circle cx="6" cy="6" r="5.5"/><path d="M3 4l2 1-1 2 2 2M7 2l1 2 2 0" stroke="#fff" stroke-width="1" fill="none"/></svg>www.clairevalconseil.ch</li>
    </ul>
    <address class="address">Rue des Vergières 27<br>1201 Geneva</address>
  </section>

  <section class="card card--back" aria-label="Card back">
    <p class="brand-name">Claireval Conseil et Comptes</p>
  </section>
</main>
</body>
</html>
```